Business Card Design

We are a manufacturing and distribution company with most of our customer base being supermarkets. We have established brand guidelines that are attached.

```html
<!DOCTYPE html>
<html lang="en">
<head>
<meta charset="utf-8">
<title>Veltoria Business Card</title>
<link href="https://fonts.googleapis.com/css2?family=Arimo:wght@400;700&display=swap" rel="stylesheet">
<style>
  :root {
    --stage: #2a2a2a;
    --card-dark: #1c1c1d;
    --card-black: #0f0f10;
    --paper: #ffffff;
    --ink: #1a1a1a;
    --red: #e31e24;
    --blue: #0a6bb5;
    --text-light: #f2f2f2;
  }
  * { margin: 0; padding: 0; box-sizing: border-box; }
  html, body {
    width: 1200px; height: 988px; overflow: hidden;
    background: var(--stage);
    font-family: "Arimo", Arial, sans-serif;
  }
  .canvas { position: relative; width: 1200px; height: 988px; }
  .card {
    position: absolute; width: 620px; height: 354px;
    border-radius: 22px; overflow: hidden;
    box-shadow: 0 14px 30px rgba(0,0,0,.55);
  }
  /* Back side */
  .card-back {
    left: 60px; top: 90px;
    background: linear-gradient(135deg, #222224 0%, var(--card-black) 60%, #1a1a1b 100%);
  }
  .card-back .brand {
    position: absolute; right: 48px; bottom: 52px;
    display: flex; align-items: center; gap: 14px;
    color: var(--text-light); font-weight: 700; font-size: 44px; letter-spacing: 3px;
  }
  .brand-square { width: 26px; height: 26px; background: currentColor; }
  /* Front side */
  .card-front { left: 520px; top: 540px; background: var(--card-dark); }
  .card-front .sweep { position: absolute; inset: 0; }
  .card-front .brand {
    position: absolute; left: 335px; right: 28px; top: 120px;
    display: flex; flex-direction: column; align-items: center; gap: 16px;
    color: var(--ink); font-weight: 700; font-size: 38px; letter-spacing: 2px;
    white-space: nowrap;
  }
  .card-front .brand .brand-square { width: 32px; height: 32px; background: var(--blue); }
  .details { position: absolute; left: 40px; top: 100px; color: var(--text-light); }
  .person-name { font-weight: 700; font-size: 30px; letter-spacing: 1px; line-height: 1; }
  .person-name .first { color: var(--red); }
  .person-name .last { color: var(--blue); }
  .person-role { font-size: 15px; margin-top: 6px; }
  .address { font-size: 15px; line-height: 1.35; margin-top: 30px; margin-left: 18px; }
  .contacts { list-style: none; margin-top: 28px; margin-left: 18px; font-size: 15px; }
  .contacts li { display: flex; align-items: center; gap: 8px; line-height: 1.5; }
  .contacts svg { width: 13px; height: 13px; fill: var(--red); }
</style>
</head>
<body>
<main class="canvas">

  <section class="card card-back" aria-label="Card back">
    <div class="brand"><span class="brand-square"></span>VELTORIA</div>
  </section>

  <section class="card card-front" aria-label="Card front">
    <svg class="sweep" viewBox="0 0 620 354" preserveAspectRatio="none" aria-hidden="true">
      <path d="M318,0 C250,120 300,300 560,354 L620,354 L620,0 Z" fill="var(--blue)"/>
      <path d="M322,0 C262,115 310,292 560,344 L620,344 L620,0 Z" fill="var(--red)"/>
      <path d="M336,0 C280,115 325,285 560,338 L620,338 L620,0 Z" fill="var(--paper)"/>
    </svg>

    <div class="brand"><span class="brand-square"></span>VELTORIA</div>

    <div class="details">
      <h1 class="person-name"><span class="first">DORIAN</span> <span class="last">KELL</span></h1>
      <p class="person-role">CEO/Founder</p>
      <p class="address">5120 Harlow Lane<br>Country Name, AB 40216</p>
      <ul class="contacts">
        <li><svg viewBox="0 0 24 24"><path d="M6.6 10.8a15 15 0 0 0 6.6 6.6l2.2-2.2a1 1 0 0 1 1-.25 11.4 11.4 0 0 0 3.6.57 1 1 0 0 1 1 1V20a1 1 0 0 1-1 1A17 17 0 0 1 3 4a1 1 0 0 1 1-1h3.5a1 1 0 0 1 1 1c0 1.25.2 2.45.57 3.57a1 1 0 0 1-.25 1z"/></svg>555-014-2290</li>
        <li><svg viewBox="0 0 24 24"><path d="M2 5h20v14H2z M2 5l10 8 10-8" /></svg>info@veltoria.com.au</li>
        <li><svg viewBox="0 0 24 24"><circle cx="12" cy="12" r="10"/></svg>www.veltoria.com.au</li>
      </ul>
    </div>
  </section>

</main>
</body>
</html>
```